Larkspur Talent IT Recruiting firm needs a business card design for Recruiters, Sourcers, and Account

We need business cards that allow us to change all contact info, names, titles (Recruiter, Sourcer, Account Manager, Director, CEO, etc) per person since we have three offices, in three cities, Phoenix, Austin, and Las Vegas. We do recruiting and contractors for IT positions (Developers, Architects, Software Engineers, Security Engineers, Help Desk, DBAs, PMs, Scrum Masters, etc.) Our client companies are very diverse from Meridian 100 to silicone Valley type start-ups.

So, while we what hip, techie, and quirky, it still needs to be professional. Primary color we use is blue, with silver as a secondary color.

Target Market(s)

IT, Technology

Industry/Entity Type

Business

Contact Information for Business Card

Company name: Larkspur Talent, Inc.
Website: www.larkspurtalent.example
Logos for Careerloop, Blipster, and Myriada

Name, Title, Office Number, Cell Number, email

Font styles to use
Serif
Sans Serif

Colors
0455a3
d5d5d5

Requirements
Nice to have
• The grey I selected below is not necessary - but, would like silver included. I included a card design (File 3: LTI early trial example.jpg) that I had started on. It's very rough, and not quite what we're looking for, but what we did like is the logo, big, maybe a bit faded, off center, goes out of frame, etc. Still looking for other ideas - you are the pros! But, just an idea of a design element we liked.

```html
<!DOCTYPE html>
<html lang="en">
<head>
<meta charset="utf-8">
<title>Larkspur Talent — Business Card</title>
<link rel="stylesheet" href="https://fonts.googleapis.com/css2?family=Cinzel:wght@400;600&family=Open+Sans:wght@400;700&display=swap">
<style>
  :root {
    --backdrop: #4a4a4c;
    --card-dark: #0c0c0d;
    --card-dark-edge: #1c1c1e;
    --card-light: #ffffff;
    --brand-blue: #0a7fd6;
    --brand-deep: #0455a3;
    --silver: #d5d5d5;
    --ink: #222426;
    --white: #ffffff;
  }
  * { box-sizing: border-box; margin: 0; padding: 0; }
  html, body {
    width: 1200px; height: 852px; overflow: hidden;
    background: var(--backdrop);
  }
  .stage {
    width: 1200px; height: 852px;
    display: flex; align-items: center; justify-content: center; gap: 40px;
  }
  .card {
    position: relative;
    width: 540px; height: 309px;
    border-radius: 14px;
    overflow: hidden;
  }
  /* Front */
  .card-front {
    background: linear-gradient(135deg, var(--card-dark-edge), var(--card-dark) 60%);
    display: flex; flex-direction: column; align-items: center; justify-content: center;
    color: var(--white);
  }
  .wordmark {
    display: flex; align-items: center; gap: 14px;
    font-family: "Cinzel", serif; font-weight: 600;
    font-size: 40px; letter-spacing: 2px; color: var(--white);
  }
  .wordmark-dot {
    width: 46px; height: 46px; border-radius: 50%;
    background: var(--brand-blue);
  }
  .tagline {
    margin-top: 30px;
    font-family: "Cinzel", serif; font-weight: 400;
    font-size: 17px; letter-spacing: 2.5px; text-transform: uppercase;
    color: var(--silver);
  }
  /* Back */
  .card-back { background: var(--card-light); color: var(--ink); }
  .emblem-field {
    position: absolute; left: -30px; top: 40px;
    width: 320px; height: 320px; border-radius: 50%;
    background: linear-gradient(180deg, var(--brand-blue), var(--brand-deep));
  }
  .contact {
    position: absolute; left: 305px; top: 42px;
    font-family: "Open Sans", sans-serif;
  }
  .person-name {
    font-weight: 700; font-size: 15px; letter-spacing: .5px;
    color: var(--brand-blue); text-transform: uppercase;
  }
  .person-title { font-size: 11px; margin-top: 2px; }
  .address { font-size: 12px; line-height: 1.4; margin-top: 14px; }
  .lines { list-style: none; margin-top: 12px; }
  .lines li {
    display: flex; align-items: center; gap: 10px;
    font-size: 12px; line-height: 1.55;
  }
  .lines svg { width: 12px; height: 12px; flex: none; }
  .socials {
    display: flex; gap: 8px; margin-top: 12px;
    font-size: 10px; font-weight: 700; color: var(--brand-blue);
  }
</style>
</head>
<body>
<main class="stage">
  <section class="card card-front" aria-label="Card front">
    <div class="wordmark"><span class="wordmark-dot"></span>LARKSPUR TALENT</div>
    <p class="tagline">Placing the Right Talent</p>
  </section>

  <section class="card card-back" aria-label="Card back">
    <div class="emblem-field" role="img" aria-label="Large brand emblem area in blue"></div>
    <div class="contact">
      <h1 class="person-name">Dana Whitlow</h1>
      <p class="person-title">CEO</p>
      <p class="address">4410 E Juniper Ave, Suite 210<br>Phoenix, AZ 85000, USA</p>
      <ul class="lines">
        <li>
          <svg viewBox="0 0 12 12"><path fill="#0455a3" d="M2.5 1h2l1 3-1.5 1a6 6 0 0 0 3 3l1-1.5 3 1v2c0 .6-.5 1-1 1A10 10 0 0 1 1.5 2c0-.6.4-1 1-1z"/></svg>
          555| 201-4478
        </li>
        <li>
          <svg viewBox="0 0 12 12"><rect x="3" y="1" width="6" height="3" fill="#0455a3"/><rect x="1" y="4" width="10" height="5" rx="1" fill="#0455a3"/><rect x="3" y="7.5" width="6" height="3.5" fill="#fff" stroke="#0455a3"/></svg>
          555| 306-8812
        </li>
        <li>
          <svg viewBox="0 0 12 12"><rect x="1" y="2.5" width="10" height="7" fill="#0455a3"/><path d="M1 2.5l5 4 5-4" fill="none" stroke="#fff"/></svg>
          dana@larkspurtalent.example
        </li>
        <li>
          <svg viewBox="0 0 12 12"><circle cx="6" cy="6" r="5" fill="none" stroke="#0455a3"/><ellipse cx="6" cy="6" rx="2.2" ry="5" fill="none" stroke="#0455a3"/><path d="M1 6h10" stroke="#0455a3"/></svg>
          www.larkspurtalent.example
        </li>
      </ul>
      <p class="socials"><span>Blipster</span><span>Careerloop</span><span>Myriada</span></p>
    </div>
  </section>
</main>
</body>
</html>
```